Business Card design for insurance broker in Denver, CO, USA

I need a business card designed using this logo that was just created. We sell life and disability income insurance to US consumers.
Looking for a professionally designed card to make use of the logo and have something to hand to prospects or new business referral sources. The card could be white, gray, black or whatever you would recommend.

Target Market(s)

US Consumers and other financial professionals that I partner with.

Industry/Entity Type

Insurance Broker

Contact Information for Business Card

Owen T. Farrow, CLU, LUTCF (please note that CLU should have a superscript R in a circle for registered trademark)
President
phone (303) 555-0187
email owen@keelbrookcover.example
4620 W. Halvern Rd, Suite 300, Alder Ridge, CO 80942
Somewhere fit in a tagline saying "Steady guidance on life, care and income protection plans" (maybe the back if it doesn't fit on the front, your call)

Font styles to use
Sans Serif

Requirements
Must have
• Must have logo in correct blue and gray colors, my name, address, phone, email. Order and placement determined by the designer.
• I just want something that looks a more professional than what I could have done using the business card designer tool on pixelbazaar.example or QuillPress, or any other do-it-yourself tool
• A regular rectangular business card with square corners is preferred
Nice to have
• I included the logos of 2 organizations I belong to (GKLS and WOBCE). They should be small, but visible on the back only. If it doesn’t look good, this is not a requirement, feel free to drop it.
Should not have
• Do not add any colors not already in the logo, except use of black and whites which are okay. If you use the logo on the back and want to make that in all black, gray or white, that may be okay as well.

```html
<!DOCTYPE html>
<html lang="en">
<head>
<meta charset="utf-8">
<title>Keelbrook Cover – Business Card</title>
<link href="https://fonts.googleapis.com/css2?family=Montserrat:wght@400;500;700&display=swap" rel="stylesheet">
<style>
  :root {
    --brand-blue: #0288d1;
    --brand-cyan: #00b2e3;
    --brand-gray: #a6a6a6;
    --ink-gray: #5c5c5c;
    --paper: #ffffff;
    --backdrop: #dcdcdc;
  }
  * { box-sizing: border-box; margin: 0; padding: 0; }
  html, body { width: 1200px; height: 800px; overflow: hidden; }
  body {
    background: var(--backdrop);
    font-family: "Montserrat", sans-serif;
    position: relative;
  }
  .card {
    position: absolute;
    top: 250px;
    width: 525px;
    height: 300px;
    overflow: hidden;
    box-shadow: 0 6px 18px rgba(0,0,0,.18);
  }
  .card--front { left: 50px; background: var(--paper); }
  .card--back {
    left: 625px;
    background: linear-gradient(120deg, var(--brand-blue) 0%, var(--brand-cyan) 45%, var(--brand-blue) 80%);
  }
  .swoosh { position: absolute; inset: 0; width: 100%; height: 100%; }

  .brand { display: flex; align-items: center; gap: 12px; white-space: nowrap; }
  .brand__dot {
    flex: none;
    width: 40px; height: 40px; border-radius: 50%;
    border: 3px solid currentColor;
  }
  .brand__name {
    font-weight: 700; font-size: 20px; line-height: 1.05;
    letter-spacing: .5px; text-transform: uppercase;
  }
  .brand__name span { display: block; }
  .card--front .brand { color: var(--brand-blue); position: absolute; left: 150px; top: 48px; }

  .contact { position: absolute; left: 150px; top: 118px; }
  .contact__name { color: var(--brand-blue); font-weight: 700; font-size: 15px; white-space: nowrap; }
  .contact__name sup { font-size: 8px; font-weight: 500; }
  .contact__title { color: var(--brand-gray); font-size: 13px; margin-top: 2px; margin-left: 60px; }
  .contact__details { margin-top: 16px; color: var(--ink-gray); font-size: 11px; line-height: 1.55; }
  .contact__row { display: flex; align-items: center; gap: 7px; }
  .contact__icon { width: 14px; height: 14px; flex: none; }

  .card--back .brand { color: var(--paper); position: absolute; left: 50%; top: 105px; transform: translateX(-50%); }
  .tagline {
    position: absolute; left: 0; right: 0; top: 180px; text-align: center;
    color: var(--paper); font-size: 13px;
  }
</style>
</head>
<body>

<section class="card card--front" aria-label="Business card front">
  <svg class="swoosh" viewBox="0 0 525 300" aria-hidden="true">
    <path d="M400 0 C410 70 460 120 525 135 L525 0 Z" fill="var(--brand-blue)"/>
    <path d="M382 0 C393 82 450 140 525 155" fill="none" stroke="var(--brand-gray)" stroke-width="4"/>
    <path d="M125 300 C115 230 65 180 0 165 L0 300 Z" fill="var(--brand-blue)"/>
    <path d="M143 300 C132 218 75 160 0 145" fill="none" stroke="var(--brand-gray)" stroke-width="4"/>
  </svg>

  <div class="brand">
    <span class="brand__dot"></span>
    <span class="brand__name"><span>Keelbrook</span><span>Cover</span></span>
  </div>

  <div class="contact">
    <p class="contact__name">Owen T. Farrow, CLU<sup>®</sup>, LUTCF</p>
    <p class="contact__title">President</p>
    <div class="contact__details">
      <p>4620 W. Halvern Rd, Suite 300,</p>
      <p>Alder Ridge, CO 80942</p>
      <p class="contact__row">
        <svg class="contact__icon" viewBox="0 0 16 16" aria-hidden="true"><circle cx="8" cy="8" r="7" fill="none" stroke="var(--brand-blue)" stroke-width="1.2"/><path d="M6 4.5 L7.5 6.5 L6.8 7.5 C7.2 8.6 7.9 9.3 9 9.8 L10 9 L11.8 10.5 L11 11.8 C8 11.6 5 8.5 4.8 5.6 Z" fill="var(--brand-blue)"/></svg>
        (303) 555-0187
      </p>
      <p class="contact__row">
        <svg class="contact__icon" viewBox="0 0 16 16" aria-hidden="true"><rect x="1" y="3.5" width="14" height="9" fill="none" stroke="var(--brand-blue)" stroke-width="1.2"/><path d="M1 3.5 L8 9 L15 3.5" fill="none" stroke="var(--brand-blue)" stroke-width="1.2"/></svg>
        owen@keelbrookcover.example
      </p>
    </div>
  </div>
</section>

<section class="card card--back" aria-label="Business card back">
  <div class="brand">
    <span class="brand__dot"></span>
    <span class="brand__name"><span>Keelbrook</span><span>Cover</span></span>
  </div>
  <p class="tagline">"Steady guidance on life, care and income protection plans"</p>
</section>

</body>
</html>
```